Personal Chef Business Card Design

My company, Simmered, is a personal in-home chef service that caters to clients' needs, but I am not a caterer. The types of services that I provide range from : weekly menus for busy families, special menus for specific diets, custom menus, private parties, intimate dinners, and brunch parties. My cooking style is seasonal and simple with the option of a variety of cuisines. I like colorful and simple business cards. My business is just getting started as I will be the only employee for now. I would like to be able to use the design on the card for my logo also. I don't know if logo design is a different service altogether.

If you can convince me to go with double-sided, then so be it, but until then, I'll stick with singe-sided.

Target Market(s)

busy families, health conscious, private parties, brunch parties, dinner parties

Industry/Entity Type

Chef

Contact Information for Business Card

Owen Talbot
owentalbot@kestrelmail.com
555-418-2937
Simmered Personal Chef Service
Serving the DC/VA/MD area

Font styles to use
Serif
Sans Serif
Decorative
Script
Other font styles liked:
• Anything

Requirements
Must have
• I will be using the illustration as my logo so that I can use it for promotional merchandise.

```html
<!DOCTYPE html>
<html lang="en">
<head>
<meta charset="utf-8">
<title>Simmered Business Card</title>
<link rel="stylesheet" href="https://fonts.googleapis.com/css2?family=Lato:wght@400;700&display=swap">
<style>
  :root {
    --backdrop: #3a302b;
    --card: #1b1b1b;
    --card-edge: #111111;
    --brand-red: #921b1d;
    --gold: #f2c75c;
    --ink-light: #ececec;
  }
  * { box-sizing: border-box; margin: 0; padding: 0; }
  html, body { width: 1200px; height: 844px; overflow: hidden; }
  body {
    background: var(--backdrop);
    font-family: 'Lato', sans-serif;
    position: relative;
  }
  .card {
    position: absolute;
    top: 262px;
    width: 520px;
    height: 300px;
    background: var(--card);
    border: 1px solid var(--card-edge);
    box-shadow: 0 10px 24px rgba(0,0,0,0.45);
  }
  .card--info { left: 50px; }
  .card--brand { left: 630px; }

  .brand-tile {
    position: absolute;
    left: 40px;
    top: 78px;
    width: 148px;
    height: 148px;
    border-radius: 8px;
    background: var(--brand-red);
    display: flex;
    align-items: center;
    justify-content: center;
    color: var(--gold);
    font-weight: 700;
    font-size: 26px;
  }
  .contact {
    position: absolute;
    left: 226px;
    top: 72px;
    color: var(--ink-light);
    font-size: 14px;
    line-height: 1.3;
  }
  .contact__name {
    color: var(--gold);
    font-size: 21px;
    font-weight: 700;
  }
  .contact__role { margin-bottom: 14px; }
  .contact__address { margin-bottom: 14px; }
  .contact__label { color: var(--gold); display: inline-block; width: 18px; }

  .brand-lockup {
    position: absolute;
    inset: 0;
    display: flex;
    flex-direction: column;
    align-items: center;
    justify-content: center;
    gap: 14px;
  }
  .brand-lockup__square {
    width: 56px;
    height: 56px;
    border-radius: 4px;
    background: var(--brand-red);
  }
  .brand-lockup__name {
    color: var(--gold);
    font-size: 40px;
    font-weight: 400;
    letter-spacing: 3px;
    text-transform: uppercase;
  }
</style>
</head>
<body>
  <section class="card card--info">
    <div class="brand-tile">Simmered</div>
    <div class="contact">
      <p class="contact__name">Owen Talbot</p>
      <p class="contact__role">Personal Chef</p>
      <p class="contact__address">Serving the DC/VA/MD area<br>Personal Chef Service</p>
      <p><span class="contact__label">T:</span>555-418-2937</p>
      <p><span class="contact__label">E:</span>owentalbot@kestrelmail.com</p>
      <p><span class="contact__label">W:</span>www.simmeredchef.com</p>
    </div>
  </section>

  <section class="card card--brand">
    <div class="brand-lockup">
      <div class="brand-lockup__square"></div>
      <p class="brand-lockup__name">Simmered</p>
    </div>
  </section>
</body>
</html>
```